Tolvik Commercial Cleaning is lookong for a new business card design.

A fresh new design that's professional and stylish. We need a serious upgrade to our business cards. I have included pictures of our existing ones. Our clients include professional individuals and business owners. We woupdblike something professional and upbeat. Please have fun and see what you come uo with.

Target Market(s)

Property managers, business owners, facility managers and other similar professionals

Industry/Entity Type

Janitorial

Contact Information for Business Card

Name, cell, office number, email, web address

Font styles to use
Sans Serif

Colors

Designer to choose colors to be used in the design.

Requirements
Must have
• please use the green color in our logo
Nice to have
• Bar code
Should not have
• Address

```html
<!DOCTYPE html>
<html lang="en">
<head>
<meta charset="utf-8">
<title>Tolvik Commercial Cleaning – Business Card</title>
<link rel="stylesheet" href="https://fonts.googleapis.com/css2?family=Open+Sans:wght@400;600;700&display=swap">
<style>
  :root {
    --backdrop: #2a2a2e;
    --brand-green: #3bb85a;
    --deep-green: #2e8f45;
    --card-dark: #222226;
    --accent-blue: #3f6fb5;
    --ghost-green: #2c3d31;
    --text-light: #f2f2f2;
    --rule: #d9d9d9;
  }
  * { box-sizing: border-box; margin: 0; padding: 0; }
  html, body {
    width: 1200px; height: 780px; overflow: hidden;
    background: var(--backdrop);
    font-family: "Open Sans", Arial, sans-serif;
  }
  .canvas {
    position: relative; width: 1200px; height: 780px;
    display: flex; flex-direction: column; align-items: center; justify-content: center; gap: 28px;
  }
  .card {
    position: relative; width: 620px; height: 354px; overflow: hidden;
    box-shadow: 0 10px 28px rgba(0,0,0,.45);
  }

  /* Front */
  .card--front {
    background: var(--brand-green);
    display: flex; align-items: center; justify-content: center; gap: 18px;
  }
  .front-mark {
    width: 34px; height: 34px; border-radius: 50%; background: var(--deep-green);
  }
  .front-name {
    font-weight: 700; font-size: 40px; color: var(--deep-green); letter-spacing: .5px;
    line-height: 1.05;
  }

  /* Back */
  .card--back { background: var(--card-dark); color: var(--text-light); }
  .ghost-name {
    position: absolute; right: -24px; bottom: -34px;
    font-weight: 700; font-size: 150px; color: var(--ghost-green); line-height: 1;
  }
  .brand-block { position: absolute; left: 40px; top: 44px; display: flex; align-items: center; gap: 12px; }
  .brand-dot { width: 18px; height: 18px; background: var(--brand-green); border-radius: 50%; }
  .brand-name { font-weight: 700; font-size: 24px; color: var(--brand-green); line-height: 1.15; }

  .person { position: absolute; right: 56px; top: 42px; text-align: right; }
  .person-name { font-weight: 700; font-size: 26px; line-height: 1.1; }
  .person-name .first { color: var(--brand-green); }
  .person-name .last { color: var(--accent-blue); }
  .person-role {
    font-size: 14px; color: var(--text-light); margin-top: 4px;
    padding-bottom: 4px; border-bottom: 1.5px solid var(--rule);
  }
  .accent-bar { position: absolute; right: 26px; top: 38px; width: 14px; height: 56px; background: var(--brand-green); }

  .divider { position: absolute; left: 40px; right: 210px; top: 178px; height: 1.5px; background: var(--rule); }

  .contact { position: absolute; left: 40px; bottom: 36px; list-style: none; font-size: 15px; line-height: 1.75; }
  .contact li { display: flex; align-items: center; gap: 10px; }
  .contact svg { width: 15px; height: 15px; fill: var(--brand-green); flex: none; }
</style>
</head>
<body>
<main class="canvas">
  <section class="card card--front" aria-label="Card front">
    <span class="front-mark"></span>
    <h1 class="front-name">Tolvik<br>Commercial Cleaning</h1>
  </section>

  <section class="card card--back" aria-label="Card back">
    <div class="ghost-name" aria-hidden="true">Tolvik</div>

    <div class="brand-block">
      <span class="brand-dot"></span>
      <p class="brand-name">Tolvik<br>Commercial Cleaning</p>
    </div>

    <div class="accent-bar"></div>
    <div class="person">
      <p class="person-name"><span class="first">Maren</span> <span class="last">Solberg</span></p>
      <p class="person-role">Director</p>
    </div>

    <div class="divider"></div>

    <ul class="contact">
      <li>
        <svg viewBox="0 0 24 24" aria-hidden="true"><path d="M6.6 10.8a15.1 15.1 0 0 0 6.6 6.6l2.2-2.2a1 1 0 0 1 1-.25 11.4 11.4 0 0 0 3.6.57 1 1 0 0 1 1 1V20a1 1 0 0 1-1 1A17 17 0 0 1 3 4a1 1 0 0 1 1-1h3.5a1 1 0 0 1 1 1c0 1.25.2 2.45.57 3.57a1 1 0 0 1-.25 1z"/></svg>
        (555) 014-2290
      </li>
      <li>
        <svg viewBox="0 0 24 24" aria-hidden="true"><path d="M3 5h18a1 1 0 0 1 1 1v12a1 1 0 0 1-1 1H3a1 1 0 0 1-1-1V6a1 1 0 0 1 1-1zm9 7.5L4 7.3V8l8 5.2L20 8v-.7z"/></svg>
        maren@tolvikcleaning.com
      </li>
      <li>
        <svg viewBox="0 0 24 24" aria-hidden="true"><path d="M12 2a10 10 0 1 0 0 20 10 10 0 0 0 0-20zm6.9 6h-3a15.6 15.6 0 0 0-1.4-3.6A8 8 0 0 1 18.9 8zM12 4c.8 1.2 1.5 2.5 1.9 4h-3.8c.4-1.5 1.1-2.8 1.9-4zM4.3 14a8.2 8.2 0 0 1 0-4h3.4a16.5 16.5 0 0 0 0 4zm.8 2h3a15.6 15.6 0 0 0 1.4 3.6A8 8 0 0 1 5.1 16zm3-8h-3a8 8 0 0 1 4.4-3.6A15.6 15.6 0 0 0 8.1 8zM12 20c-.8-1.2-1.5-2.5-1.9-4h3.8c-.4 1.5-1.1 2.8-1.9 4zm2.3-6H9.7a14.7 14.7 0 0 1 0-4h4.6a14.7 14.7 0 0 1 0 4zm.2 5.6a15.6 15.6 0 0 0 1.4-3.6h3a8 8 0 0 1-4.4 3.6zm1.8-5.6a16.5 16.5 0 0 0 0-4h3.4a8.2 8.2 0 0 1 0 4z"/></svg>
        www.tolvikcleaning.com
      </li>
    </ul>
  </section>
</main>
</body>
</html>
```